Copper Field Agency Website - Wordpress Web UPDATED BRIEF

FINAL LOGO UPLOADED - please look to this as reference for how we would like the site to look and feel.

We are a digital marketing agency - looking to have a new website built. We are looking for a simple one page feel of site that will allow us to grow it later. (Feel free to take some liberties with that if your imagination veers off) Must be very, playful, bold, sleek and easily integrate video. Wordpress only.

Overview:

Copper Field is a creative constellation. We are built on what's great about the shared economy. With access to thousands of content creators, designers, technicians, writers, strategists and other creatives around the world, we are built differently than a traditional “brick and mortar” Marketing Agency. We provide the traditional services our clients have come to expect, without the “5X factor” of covering the overhead common in the old agency model. We believe even better work can be created in collaboration with our clients and by passing those savings back to them for their use. Our clients pay for our art, our work and our passion –not our furniture.

"Copper Field, Let's Build Together"

Target Market(s)

companies looking for creative agency help, video production, creative consulting and coaching

Industry/Entity Type

Digital Marketing

Coding

Coded - Design and coding required

Number of Pages Required

1 page

Font styles to use
Sans Serif

Colors
3277b5
33a6d7
ec1f27

Requirements
Must have
• Wordpress design is a must. Looking for a one sheet homepage - with sections that are all on the main front page. We will have videos to embed, and should be able to have client logos and easy access to show a variety of our creative work.
• Please look to the logo for how we would like the site to feel.
• Please think "icon process flow" instead of blocks of text (which we used to have). Use the text to explain what the process flow should represent - don't actually copy paste the text but show it visually in icons.
Nice to have
• innovation around how we show video content. solid colors complementary to our palette and aesthetic.
Should not have
• Standard HTML coding

```html
<!DOCTYPE html>
<html lang="en">
<head>
<meta charset="utf-8">
<title>Copper Field – Digital Marketing</title>
<link rel="stylesheet" href="https://fonts.googleapis.com/css2?family=Oswald:wght@400;500&family=Open+Sans:wght@400;600&display=swap">
<style>
:root{
  --navy:#1d4f9c;
  --blue:#2763ae;
  --sky:#2f93d1;
  --red:#e3121f;
  --pale:#d6e9f6;
  --ink:#3a3a3a;
  --muted:#8b8b8b;
  --white:#ffffff;
  --head:'Oswald',sans-serif;
  --body:'Open Sans',sans-serif;
}
*{margin:0;padding:0;box-sizing:border-box}
html,body{width:1200px;height:4289px;overflow:hidden;background:var(--white)}
body{position:relative;font-family:var(--body);color:var(--ink)}
.abs{position:absolute}
.shape{position:absolute;left:0;top:0;width:1200px;height:4289px}

/* header */
.nav{position:absolute;top:28px;left:373px;display:flex;gap:0}
.nav a,.foot-nav a{font-family:var(--head);font-size:16px;color:var(--navy);text-decoration:none;font-weight:500;position:absolute;white-space:nowrap}
.brand{position:absolute;left:160px;top:0;width:150px;height:160px}
.brand-disc{position:absolute;left:8px;top:0;width:134px;height:134px;border-radius:50%;background:var(--blue);border:5px solid var(--white)}
.brand-name{position:absolute;left:0;top:112px;width:150px;text-align:center;font-family:var(--head);font-size:27px;font-weight:500;color:var(--white);letter-spacing:.5px}

/* hero */
.hero-text{position:absolute;left:0;width:1200px;text-align:center;color:var(--white);font-family:var(--head)}
.hero-kicker{top:380px;font-size:40px;font-weight:400}
.hero-title{top:432px;font-size:78px;font-weight:500;letter-spacing:.5px}
.hero-arrow{position:absolute;left:126px;top:328px;width:52px;height:52px;border-radius:50%;background:rgba(255,255,255,.55)}
.hero-arrow.next{left:1008px}

/* section titles */
.sec-title{position:absolute;left:0;width:1200px;text-align:center;font-family:var(--head);font-size:40px;font-weight:500;color:var(--blue)}
.sec-title::after{content:"";display:block;width:50px;height:3px;margin:8px auto 0;background:currentColor}
.sec-title.on-blue{color:var(--white)}
.sec-title.red{color:var(--red)}

/* about */
.about-art{position:absolute;left:133px;top:765px;width:441px;height:441px;border-radius:12px;background:radial-gradient(circle at 55% 45%,#6f63e0 0,#c7b9f2 45%,#f4f2fb 75%)}
.about-title{position:absolute;left:599px;top:785px;font-family:var(--head);font-size:46px;font-weight:500;color:var(--blue)}
.about-copy{position:absolute;left:600px;top:876px;width:476px;font-size:14px;line-height:23px;color:var(--ink)}
.about-copy p+p{margin-top:23px}

/* services */
.service{position:absolute;width:420px}
.service svg{position:absolute;left:0;top:0;width:64px;height:64px}
.service h3{position:absolute;left:78px;top:0;font-family:var(--head);font-size:20px;font-weight:400;color:var(--white)}
.service p{position:absolute;left:78px;top:34px;width:340px;font-size:13px;line-height:19px;color:var(--white)}

/* videos */
.video{position:absolute;top:2072px;width:446px;height:274px;border:5px solid var(--white);box-shadow:0 0 6px rgba(0,0,0,.35)}
.video-frame{width:100%;height:100%}
.play{position:absolute;left:50%;top:50%;width:64px;height:64px;margin:-32px 0 0 -32px;border-radius:50%;background:var(--white)}
.play::after{content:"";position:absolute;left:26px;top:20px;border-left:18px solid #333;border-top:12px solid transparent;border-bottom:12px solid transparent}
.chev{position:absolute;width:30px;height:52px}

/* gallery */
.tile{position:absolute;border:1px solid var(--white)}

/* clients */
.client{position:absolute;width:220px;text-align:center;font-family:var(--head);font-size:24px;font-weight:500;color:#8a8a8a}

/* contact */
.contact-bg{position:absolute;left:0;top:3520px;width:1200px;height:630px;background:linear-gradient(135deg,#3a74bf 0%,#2559a6 55%,#1f4f9a 100%)}
.field{position:absolute;left:153px;width:434px;height:45px;background:var(--white);border:none;font-family:var(--body);font-size:14px;color:var(--muted);padding:12px 20px}
.field.msg{height:91px}
.submit{position:absolute;left:153px;top:3967px;width:172px;height:44px;background:var(--red);color:var(--white);font-family:var(--body);font-weight:600;font-size:16px;text-align:center;line-height:44px}
.info{position:absolute;left:705px;color:var(--white)}
.info h4{font-family:var(--body);font-weight:400;font-size:15px;letter-spacing:.3px}
.info p{font-size:16px;margin-top:1px}
.info-icon{position:absolute;left:652px;width:36px;height:36px}
.social{position:absolute;top:3928px;width:36px;height:36px;border-radius:50%;border:2px solid var(--white)}

/* footer */
.foot-brand{position:absolute;left:148px;top:4100px;width:140px;height:160px}
.foot-brand .brand-disc{left:10px;width:120px;height:120px;background:var(--blue)}
.foot-brand .brand-name{top:100px;width:140px;font-size:25px;color:var(--navy)}
.copyright{position:absolute;left:358px;top:4198px;font-size:13px;color:var(--navy)}
</style>
</head>
<body>

<!-- header & hero -->
<svg class="shape" viewBox="0 0 1200 4289" aria-hidden="true">
  <rect x="0" y="84" width="210" height="30" fill="var(--sky)"/>
</svg>
<div class="abs" role="img" aria-label="Photo of a creative team working together over laptops and notes"
     style="left:0;top:91px;width:1200px;height:641px;clip-path:polygon(0 0,100% 0,100% 97.5%,0 100%);background:linear-gradient(120deg,#1d1d22 0%,#3b3633 40%,#5a4a3e 70%,#2a2a2f 100%)"></div>
<svg class="shape" viewBox="0 0 1200 4289" aria-hidden="true">
  <polygon points="0,666 620,702 0,734" fill="var(--red)"/>
</svg>

<nav class="nav" style="left:0;top:28px;width:1200px">
  <a style="left:373px">ABOUT US</a>
  <a style="left:478px">SERVICES</a>
  <a style="left:577px">GALLERY</a>
  <a style="left:672px">VIDEO</a>
  <a style="left:749px">CLIENTS</a>
  <a style="left:839px">CONTACT US</a>
</nav>

<div class="brand">
  <div class="brand-disc"></div>
  <div class="brand-name">COPPER FIELD</div>
</div>

<div class="hero-arrow"><svg width="52" height="52" viewBox="0 0 52 52"><polyline points="30,17 21,26 30,35" fill="none" stroke="#222" stroke-width="2.5"/></svg></div>
<div class="hero-arrow next"><svg width="52" height="52" viewBox="0 0 52 52"><polyline points="22,17 31,26 22,35" fill="none" stroke="#222" stroke-width="2.5"/></svg></div>
<div class="hero-text hero-kicker">WELCOME TO COPPER FIELD</div>
<div class="hero-text hero-title">DIGITAL MARKETING</div>
<svg class="abs" style="left:585px;top:545px" width="30" height="50" viewBox="0 0 30 50" aria-hidden="true">
  <line x1="15" y1="2" x2="15" y2="46" stroke="#fff" stroke-width="2"/>
  <polyline points="4,35 15,46 26,35" fill="none" stroke="#fff" stroke-width="2"/>
</svg>

<!-- about -->
<div class="about-art" role="img" aria-label="Isometric illustration of a marketing team around a laptop with charts and a megaphone"></div>
<h2 class="about-title">ABOUT US</h2>
<div class="about-copy">
  <p>Copper Field is a creative constellation. We are built on what's great about the shared economy. With access to thousands of content creators, designers, technicians, writers, strategists and other creatives around the world, we are built differently than a traditional “brick and mortar” Marketing Agency.</p>
  <p>We provide the traditional services our clients have come to expect, without the “5X factor” of covering the overhead common in the old agency model. We believe even better work can be created in collaboration with our clients and by passing those savings back to them for their use. Our clients pay for our art, our work and our passion –not our furniture.</p>
</div>

<!-- services -->
<svg class="shape" viewBox="0 0 1200 4289" aria-hidden="true">
  <defs>
    <linearGradient id="svcGrad" x1="0" y1="0" x2="1" y2="1">
      <stop offset="0" stop-color="#2e92d0"/>
      <stop offset="1" stop-color="#2659a7"/>
    </linearGradient>
  </defs>
  <polygon points="0,1323 1200,1265 1200,1897 0,1897" fill="url(#svcGrad)"/>
  <polygon points="0,1886 600,1897 0,1960" fill="var(--red)"/>
</svg>
<h2 class="sec-title on-blue" style="top:1344px">OUR SERVICES</h2>

<div class="service" style="left:176px;top:1452px">
  <svg viewBox="0 0 64 64" fill="none" stroke="#fff" stroke-width="2"><circle cx="32" cy="36" r="20"/><ellipse cx="32" cy="36" rx="9" ry="20"/><line x1="12" y1="36" x2="52" y2="36"/><line x1="15" y1="26" x2="49" y2="26"/><line x1="15" y1="46" x2="49" y2="46"/><path d="M14 20 Q32 2 50 20"/></svg>
  <h3>DISCOVERY</h3>
  <p>Pellentesque faucibus Ut accumsan ultricies elit Maecenas at justo id velit placerat molestie</p>
</div>
<div class="service" style="left:644px;top:1452px">
  <svg viewBox="0 0 64 64" fill="none" stroke="#fff" stroke-width="2"><rect x="6" y="6" width="40" height="52"/><line x1="12" y1="16" x2="38" y2="16"/><line x1="12" y1="24" x2="30" y2="24"/><line x1="12" y1="32" x2="26" y2="32"/><line x1="12" y1="44" x2="24" y2="44"/><path d="M54 16 L30 46 L26 52 L32 48 L58 20 Z"/></svg>
  <h3>CONTENT</h3>
  <p>Pellentesque faucibus Ut accumsan ultricies elit Maecenas at justo id velit placerat molestie</p>
</div>
<div class="service" style="left:174px;top:1596px">
  <svg viewBox="0 0 64 64" fill="none" stroke="#fff" stroke-width="2"><path d="M22 42 Q10 32 14 20 Q20 6 32 6 Q44 6 50 20 Q54 32 42 42 Z"/><rect x="24" y="44" width="16" height="6"/><rect x="26" y="52" width="12" height="5"/><line x1="32" y1="12" x2="32" y2="40"/><line x1="22" y1="22" x2="42" y2="22"/><line x1="4" y1="24" x2="9" y2="24"/><line x1="55" y1="24" x2="60" y2="24"/></svg>
  <h3>STRATEGY</h3>
  <p>Pellentesque faucibus Ut accumsan ultricies elit Maecenas at justo id velit placerat molestie</p>
</div>
<div class="service" style="left:644px;top:1596px">
  <svg viewBox="0 0 64 64" fill="none" stroke="#fff" stroke-width="2"><circle cx="32" cy="30" r="10"/><path d="M32 6 L36 12 L44 10 L45 18 L53 21 L49 28 L54 35 L46 38 L45 46 L37 44 L32 50 L27 44 L19 46 L18 38 L10 35 L15 28 L11 21 L19 18 L20 10 L28 12 Z"/><line x1="30" y1="50" x2="30" y2="58"/></svg>
  <h3>PRODUCTION</h3>
  <p>Pellentesque faucibus Ut accumsan ultricies elit Maecenas at justo id velit placerat molestie</p>
</div>
<div class="service" style="left:176px;top:1734px">
  <svg viewBox="0 0 64 64" fill="none" stroke="#fff" stroke-width="2"><rect x="6" y="8" width="52" height="50"/><line x1="22" y1="8" x2="22" y2="58"/><line x1="12" y1="16" x2="16" y2="16"/><line x1="12" y1="26" x2="16" y2="26"/><line x1="12" y1="36" x2="16" y2="36"/><line x1="12" y1="46" x2="16" y2="46"/><rect x="28" y="14" width="24" height="8"/><rect x="28" y="28" width="24" height="8"/><rect x="28" y="42" width="24" height="8"/></svg>
  <h3>PROJECT MANAGEMENT</h3>
  <p>Pellentesque faucibus Ut accumsan ultricies elit Maecenas at justo id velit placerat molestie</p>
</div>
<div class="service" style="left:644px;top:1734px">
  <svg viewBox="0 0 64 64" fill="none" stroke="#fff" stroke-width="2"><rect x="4" y="16" width="40" height="30"/><line x1="18" y1="46" x2="16" y2="54"/><line x1="30" y1="46" x2="32" y2="54"/><line x1="12" y1="54" x2="36" y2="54"/><rect x="30" y="4" width="28" height="20"/><circle cx="24" cy="28" r="5"/><path d="M15 42 Q24 32 33 42"/><rect x="46" y="30" width="14" height="24"/></svg>
  <h3>PAID MEDIA AND COACHING</h3>
  <p>Pellentesque faucibus Ut accumsan ultricies elit Maecenas at justo id velit placerat molestie</p>
</div>

<!-- videos -->
<h2 class="sec-title" style="top:1972px">OUR VIDEOS</h2>
<svg class="chev" style="left:97px;top:2178px" viewBox="0 0 30 52" aria-hidden="true"><polyline points="24,4 6,26 24,48" fill="none" stroke="#222" stroke-width="2.5"/></svg>
<svg class="chev" style="left:1084px;top:2178px" viewBox="0 0 30 52" aria-hidden="true"><polyline points="6,4 24,26 6,48" fill="none" stroke="#222" stroke-width="2.5"/></svg>
<div class="video" style="left:145px">
  <div class="video-frame" role="img" aria-label="Video still: hand touching a glowing digital marketing interface" style="background:linear-gradient(135deg,#0c1a33 0%,#2b4f7c 50%,#11223e 100%)"></div>
  <div class="play"></div>
</div>
<div class="video" style="left:616px">
  <div class="video-frame" role="img" aria-label="Video still: hands typing on a laptop keyboard" style="background:linear-gradient(135deg,#c9c9c9 0%,#6d6f74 45%,#2c2d31 100%)"></div>
  <div class="play"></div>
</div>

<!-- gallery -->
<svg class="shape" viewBox="0 0 1200 4289" aria-hidden="true">
  <polygon points="0,2413 1200,2413 1200,3068 0,3122" fill="var(--pale)"/>
  <polygon points="720,3098 1200,3062 1200,3124" fill="var(--blue)"/>
</svg>
<h2 class="sec-title red" style="top:2494px">OUR GALLERY</h2>
<div class="tile" role="img" aria-label="Hands on a tablet with floating social media icons" style="left:143px;top:2593px;width:354px;height:382px;background:linear-gradient(160deg,#4d5a68 0%,#8c7a66 55%,#d59a52 100%)"></div>
<div class="tile" role="img" aria-label="Laptop screen reading digital marketing" style="left:509px;top:2593px;width:182px;height:183px;background:linear-gradient(180deg,#2a5fb0 0%,#e88a4a 50%,#b8c2d0 100%)"></div>
<div class="tile" role="img" aria-label="Desk with laptop showing charts, notebook and coffee" style="left:701px;top:2593px;width:374px;height:183px;background:linear-gradient(135deg,#3a3a3a 0%,#9a9a98 50%,#e6e4e0 100%)"></div>
<div class="tile" role="img" aria-label="Colourful glowing cubes on a dark surface" style="left:509px;top:2791px;width:182px;height:183px;background:linear-gradient(160deg,#0e1424 0%,#2d3e5a 55%,#6a4c8a 100%)"></div>
<div class="tile" role="img" aria-label="Small rocket launching from a laptop keyboard" style="left:701px;top:2791px;width:182px;height:183px;background:linear-gradient(180deg,#8fb6c2 0%,#d9d4c8 60%,#8a7c6a 100%)"></div>
<div class="tile" role="img" aria-label="Laptop and coffee cup on a wooden desk" style="left:894px;top:2791px;width:181px;height:183px;background:linear-gradient(135deg,#d8d8d6 0%,#9b9a96 55%,#6a5a48 100%)"></div>

<!-- clients -->
<h2 class="sec-title" style="top:3150px">OUR CLIENTS</h2>
<div class="client" style="left:128px;top:3268px">Harbourline</div>
<div class="client" style="left:368px;top:3268px">Velmora</div>
<div class="client" style="left:607px;top:3268px">Kindred Circle</div>
<div class="client" style="left:847px;top:3268px">Aldwick Assure</div>
<div class="client" style="left:128px;top:3378px">Brisko</div>
<div class="client" style="left:368px;top:3378px">Tagwise</div>
<div class="client" style="left:607px;top:3378px">Norvik</div>
<div class="client" style="left:847px;top:3378px">Ashby Mutual</div>

<!-- contact -->
<div class="contact-bg" role="img" aria-label="Deep blue photographic backdrop for the contact section"></div>
<h2 class="sec-title on-blue" style="top:3596px">CONTACT US</h2>
<div class="field" style="top:3698px">Name</div>
<div class="field" style="top:3750px">Email address</div>
<div class="field" style="top:3802px">Subject</div>
<div class="field msg" style="top:3856px">Message</div>
<div class="submit">SUBMIT</div>

<svg class="info-icon" style="top:3714px" viewBox="0 0 36 36" fill="none" stroke="#fff" stroke-width="1.6" aria-hidden="true"><path d="M18 32 C10 22 8 18 8 13 A10 10 0 0 1 28 13 C28 18 26 22 18 32 Z"/><circle cx="18" cy="13" r="4"/><ellipse cx="18" cy="32" rx="14" ry="3"/></svg>
<div class="info" style="top:3698px"><h4>ADDRESS</h4><p>42 Linden Avenue, Suite 3, Austin TX 73301</p></div>
<svg class="info-icon" style="top:3784px" viewBox="0 0 36 36" fill="none" stroke="#fff" stroke-width="1.6" aria-hidden="true"><path d="M6 4 L13 4 L16 12 L12 15 Q16 23 21 25 L24 21 L32 24 L32 31 Q18 34 9 24 Q2 14 6 4 Z"/></svg>
<div class="info" style="top:3768px"><h4>PHONE</h4><p>555.014.2780</p></div>
<svg class="info-icon" style="top:3856px" viewBox="0 0 36 36" fill="none" stroke="#fff" stroke-width="1.6" aria-hidden="true"><rect x="3" y="8" width="30" height="21"/><polyline points="3,8 18,21 33,8"/></svg>
<div class="info" style="top:3838px"><h4>EMAIL US</h4><p>hello@copperfield.example</p></div>
<div class="social" style="left:661px"></div>
<div class="social" style="left:704px"></div>
<div class="social" style="left:748px"></div>
<div class="social" style="left:791px"></div>
<div class="social" style="left:834px"></div>

<!-- footer -->
<svg class="shape" viewBox="0 0 1200 4289" aria-hidden="true">
  <polygon points="0,4150 1200,4108 1200,4289 0,4289" fill="var(--white)"/>
  <polygon points="620,4124 1200,4058 1200,4108" fill="var(--red)"/>
</svg>
<div class="foot-brand">
  <div class="brand-disc"></div>
  <div class="brand-name">COPPER FIELD</div>
</div>
<nav class="foot-nav">
  <a style="left:358px;top:4162px">ABOUT US</a>
  <a style="left:461px;top:4162px">SERVICES</a>
  <a style="left:562px;top:4162px">GALLERY</a>
  <a style="left:656px;top:4162px">VIDEO</a>
  <a style="left:734px;top:4162px">CLIENTS</a>
  <a style="left:823px;top:4162px">CONTACT US</a>
</nav>
<div class="copyright">© 2019 Copper Field&nbsp;&nbsp;All right reserved</div>

</body>
</html>
```